Agrarhandel benötigt Homepage
Zielgruppe
Wir sind ein Agrarhandel mit einem Warenumschlagslager im Sinne eines klassischen Einzelhandels und vertreiben Produkte an Landwirte.
Wir vertreiben folgende Hauptproduktgruppen:
Einzelfuttermittel
wie z.B. Sojaexktraktionsschrot. Die einzelnen Produkte könnten z.B. wie die Futtermittel auf folgender Seite dargestellt werden (https://www.kornprobe-beispiel.eu/de/produkt/trelomixan)
Mischfuttermittel
Hier bieten wir unseren Kunden an, individuelles Mischfutter auf Basis unserer Einzelfuttermittel herzustellen.
Weitere Details und weitere Produktbereiche habe ich in einer Powerpoint-Übersicht dargestellt.
Neben diesen Produkten wollen wir uns als Familienunternehmen selbst vorstellen. Zudem betreiben wir in unserer Familie zusätzlich einen Milchviehbetrieb den wir ebenfalls hervorheben möchten, da wir unseren Kunden gegenüber einerseits als Zulieferer aber auch als Kollege auftreten wollen.
Einzelfuttermittel: Hier können wir durch unsere Unabhängigkeit punkten, da wir nicht abhängig von bestimmten Lieferanten sind und dementsprechend unabhängig beraten können. Wir untersuchen im Vergleich zu unseren Wettbewerben die Qualität der Futtermittel bis ins Detail und können daher eine Transparenz bieten, die Konkurrenten in der Regel nicht bieten können. Unser Warenumschlagsplatz mit moderner Technik ermöglicht es uns äußerst kosteneffizient die Waren umschlagen und ausliefern zu können.
Mischfuttermittel: Auf Basis der vorhandenen Einzelfuttermittel stellen wir je nach Kundenwunsch individuelle Mischfutter her. Wir arbeiten mit offenen Deklarationen, sodass unsere Kunden jederzeit nachvollziehen können, ob auch die Einzelfuttermittel verwendet wurden, die sie bestellt haben und keine billigen Ersatzprodukte verwendet wurden.
Zudem sind wir BT und HUPA zertifiziert. Die aktuellen für unser Unternehmen ausgestellten Zertifikate müssen für unsere Kunden als Download zur Verfügung stehen. Statt dem HUPA-Logo bitte das ..
Aufgabenstellung
Wir möchten gerne ein zeitgemäße Homepage, jedoch muss auch berücksichtigt werden, dass unsere Kunden eher konservativ denken.

```html
<!DOCTYPE html>
<html lang="de">
<head>
<meta charset="utf-8">
<title>Feldhof Agrarhandel – Seitenentwürfe</title>
<link rel="stylesheet" href="https://fonts.googleapis.com/css2?family=Inter:wght@400;500;600;700;800&family=Archivo:wght@800;900&display=swap">
<style>
:root{
  --ink:#232323;
  --yellow:#f2cb1d;
  --amber:#f2a80d;
  --orange:#f4a20a;
  --line:#d6d6d6;
  --logo:#2b7ccb;
  --paper:#ffffff;
  --field1:#6a4a1c;
  --field2:#c98a2e;
  --field3:#e9b453;
}
*{box-sizing:border-box;margin:0;padding:0}
html,body{width:1200px;height:1161px;overflow:hidden;background:var(--paper);font-family:"Inter",sans-serif;color:var(--ink)}
.sheet{position:absolute;left:0;top:0;width:1960px;height:1897px;transform:scale(.6122);transform-origin:0 0}
.page{position:absolute;width:556px}
.page *{position:absolute}
.page .flow,.page .flow *{position:static}

/* header */
.hdr{left:0;top:0;width:100%;height:58px}
.hdr-tab{left:0;top:0;width:32px;height:55px;background:var(--amber)}
.hdr-bar{left:40px;right:0;top:0;height:58px;background:var(--ink);border-bottom:4px solid var(--line)}
.logo{font-family:"Inter",sans-serif;font-weight:800;color:var(--logo);letter-spacing:-.5px}
.hdr .logo{left:22px;top:13px;font-size:21px}
.nav{right:18px;top:24px;display:flex;gap:8px;align-items:center}
.nav a{position:static;font-size:6.4px;font-weight:700;color:#fff;text-transform:uppercase;text-decoration:none}
.nav a.on{color:var(--amber)}
.nav svg{position:static;width:10px;height:10px;margin-left:6px}

/* photo areas */
.ph{background:linear-gradient(160deg,var(--field3),var(--field2) 55%,var(--field1))}
.ph.sky{background:linear-gradient(180deg,#d7b98a,#c9914a 45%,#6f5a25)}
.ph.green{background:linear-gradient(170deg,#f0c77a,#9c8a3a 50%,#3f4a1e)}
.ph.seed{background:linear-gradient(135deg,#6d6a52,#a36a3a 50%,#3d3b2a)}
.ph.hands{background:linear-gradient(135deg,#c27d5a,#e1b063 50%,#8d3b3b)}
.ph.dark{background:linear-gradient(170deg,#d89a45,#7a4a18 60%,#2e2212)}

.btn{background:var(--yellow);border-radius:8px;font-size:8px;font-weight:700;text-align:center;color:var(--ink)}
.tiny{font-size:4.6px;line-height:1.35;color:#fff}

/* footer */
.ftr{left:0;width:100%;height:176px}
.ftr-body{left:0;top:0;width:100%;height:154px;background:var(--ink)}
.ftr-strip{left:0;top:154px;width:100%;height:22px;background:var(--yellow);font-size:5px;font-weight:600;text-align:center;line-height:22px}
.ftr-in{left:50%;top:0;width:556px;height:154px;margin-left:-278px}
.vline{width:1px;height:70px;background:#cfcfcf;top:27px}
.vline::before,.vline::after{content:"";position:absolute;left:-2px;width:5px;height:5px;border-radius:50%;background:#cfcfcf}
.vline::before{top:-2px}.vline::after{bottom:-2px}
.ftr-title{left:182px;top:28px;font-size:9px;font-weight:500;color:#fff}
.field{height:10px;background:#e4e4e4;font-size:4.5px;line-height:10px;padding-left:4px;color:#555}
.send{left:313px;top:70px;width:58px;height:10px;background:var(--yellow);border-radius:2px;font-size:5px;font-weight:700;line-height:10px;text-align:center}
.info{left:405px;top:50px;display:flex;flex-direction:column;gap:3px}
.info span{position:static;display:flex;align-items:center;gap:4px;font-size:4.6px;color:#fff}
.info svg{position:static;width:6px;height:6px}
.ftr .logo{left:0;width:100%;top:98px;text-align:center;font-size:19px}
.socials{left:0;width:100%;top:134px;display:flex;justify-content:center;gap:2px}
.socials i{position:static;display:block;width:8px;height:8px;background:#fff;border-radius:1.5px}
</style>
</head>
<body>
<div class="sheet">

<!-- ===== Page: Landwirt ===== -->
<section class="page" style="left:80px;top:12px;height:970px">
  <header class="hdr"><span class="hdr-tab"></span><div class="hdr-bar"><span class="logo">Feldhof</span><nav class="nav"><a class="on">Landwirt</a><a>Geschäftspartner</a><a>Lieferanten</a><a>Produkte</a><a>Firmenpräsentation</a><svg viewBox="0 0 10 10"><circle cx="4" cy="4" r="3" fill="none" stroke="#fff" stroke-width="1.3"/><path d="M6.2 6.2 9 9" stroke="#fff" stroke-width="1.4"/></svg></nav></div></header>
  <div class="ph" role="img" aria-label="Getreidefeld im Abendlicht" style="left:0;top:62px;width:556px;height:160px"></div>
  <p style="left:0;width:556px;top:88px;text-align:center;font-size:7px;color:#fff">LOREM IPSUM</p>
  <h1 style="left:0;width:556px;top:98px;text-align:center;font-family:'Archivo',sans-serif;font-weight:900;font-size:15px;color:var(--amber)">CONSECTETUR ADIPISCING ELIT</h1>
  <p class="tiny" style="left:188px;width:180px;top:121px;text-align:center;font-weight:700;font-size:5px">Excepteur sint occaecat cupidatat non proident, sunt in culpa qui officia deserunt mollit anim id es</p>
  <span class="btn" style="left:256px;top:145px;width:44px;height:10px"></span>
  <div class="ph hands" role="img" aria-label="Hände mit Weizenähren" style="left:135px;top:188px;width:91px;height:62px"></div>
  <div class="ph sky" role="img" aria-label="Strohballen auf dem Feld" style="left:232px;top:188px;width:91px;height:62px"></div>
  <div class="ph" role="img" aria-label="Weizenähren" style="left:329px;top:188px;width:91px;height:62px"></div>
  <p style="left:135px;top:278px;width:120px;font-size:11px;font-weight:700;line-height:1.2">Excepteur sint occaecat cupidatat non proident, sunt in culpa</p>
  <svg style="left:264px;top:266px" width="156" height="78" viewBox="0 0 156 78"><path d="M22 0H156V78H22L0 39Z" fill="var(--yellow)"/></svg>
  <p class="tiny" style="left:286px;top:280px;width:126px">Sed ut perspiciatis unde omnis iste natus error sit voluptatem accusantium doloremque laudantium, to</p>
  <p class="tiny" style="left:286px;top:304px;width:126px">Sed ut perspiciatis unde omnis iste natus error sit voluptatem accusantium doloremque laudantium, to</p>

  <svg style="left:0;top:374px" width="556" height="216" viewBox="0 0 556 216"><path d="M0 0H556V216L0 141Z" fill="var(--ink)"/></svg>
  <h2 style="left:135px;top:398px;font-size:13px;font-weight:500;color:#fff">Warum Uns Wählen?</h2>
  <p class="tiny" style="left:135px;top:422px;width:180px">Excepteur sint occaecat cupidatat non proident, sunt in culpa qui officia deserunt mollit anim id es</p>
  <div style="left:135px;top:445px;width:200px;height:70px">
    <i style="left:0;top:2px;width:8px;height:8px;border-radius:50%;background:var(--yellow)"></i>
    <p class="tiny" style="left:14px;top:0;width:60px"><b>Lorem Ipsum</b><br>Excepteur sint occaecat cupidatat non proident, sunt in culpa</p>
    <i style="left:87px;top:2px;width:8px;height:8px;border-radius:50%;background:var(--yellow)"></i>
    <p class="tiny" style="left:101px;top:0;width:60px"><b>Lorem Ipsum</b><br>Excepteur sint occaecat cupidatat non proident, sunt in culpa</p>
    <i style="left:0;top:37px;width:8px;height:8px;border-radius:50%;background:var(--yellow)"></i>
    <p class="tiny" style="left:14px;top:35px;width:60px"><b>Lorem Ipsum</b><br>Excepteur sint occaecat cupidatat non proident, sunt in culpa</p>
    <i style="left:87px;top:37px;width:8px;height:8px;border-radius:50%;background:var(--yellow)"></i>
    <p class="tiny" style="left:101px;top:35px;width:60px"><b>Lorem Ipsum</b><br>Excepteur sint occaecat cupidatat non proident, sunt in culpa</p>
  </div>
  <span class="btn" style="left:244px;top:522px;width:42px;height:10px"></span>
  <span style="left:342px;top:398px;width:189px;height:130px;background:var(--yellow);border-radius:4px"></span>
  <div class="ph dark" role="img" aria-label="Mähdrescher bei der Ernte" style="left:335px;top:405px;width:190px;height:128px"></div>

  <h2 style="left:0;width:556px;top:596px;text-align:center;font-size:12px;font-weight:600">Die Leute Sagen Über Uns</h2>
  <span style="left:0;top:650px;width:80px;height:76px;background:var(--yellow);border-radius:0 10px 10px 0"></span>
  <svg style="left:135px;top:645px" width="286" height="81" viewBox="0 0 286 81"><path d="M0 28 L276 0 Q286 0 286 10 V69 Q286 81 274 81 H12 Q0 81 0 69Z" fill="var(--yellow)"/></svg>
  <svg style="left:470px;top:646px" width="86" height="80" viewBox="0 0 86 80"><path d="M10 30 L86 0 V80 H10 Q0 80 0 70 V42 Q0 34 10 30Z" fill="var(--yellow)"/></svg>
  <span role="img" aria-label="Kundenporträt" style="left:24px;top:620px;width:40px;height:40px;border-radius:50%;background:#e9e9e9;border:2px solid #fff;box-shadow:0 0 0 1px #bbb"></span>
  <span role="img" aria-label="Kundenporträt" style="left:366px;top:618px;width:40px;height:40px;border-radius:50%;background:#e9e9e9;border:2px solid #fff;box-shadow:0 0 0 1px #bbb"></span>
  <p class="tiny" style="left:166px;top:678px;width:230px">Sed ut perspiciatis unde omnis iste natus error sit voluptatem accusantium doloremque laudantium, to</p>
  <p class="tiny" style="left:166px;top:694px;width:230px">Sed ut perspiciatis unde omnis iste natus error sit voluptatem accusantium doloremque laudantium, to</p>
  <span style="left:226px;top:749px;width:28px;height:3px;background:var(--ink);border-radius:2px"></span>
  <span style="left:263px;top:749px;width:28px;height:3px;background:var(--yellow);border-radius:2px"></span>
  <span style="left:300px;top:749px;width:28px;height:3px;background:var(--yellow);border-radius:2px"></span>

  <footer class="ftr" style="top:793px">
    <div class="ftr-body"></div>
    <div class="ftr-in">
      <span class="vline" style="left:165px"></span><span class="vline" style="left:390px"></span>
      <h3 class="ftr-title">Kontak Uns</h3>
      <span class="field" style="left:182px;top:48px;width:58px">Name</span>
      <span class="field" style="left:248px;top:48px;width:58px">Email</span>
      <span class="field" style="left:315px;top:48px;width:58px">Telefonnummer</span>
      <span class="field" style="left:182px;top:66px;width:124px;height:14px;line-height:14px">Nachricht</span>
      <span class="send">Schicken</span>
      <div class="info"><span><svg viewBox="0 0 6 6"><path d="M3 6 1 3A2 2 0 1 1 5 3Z" fill="#fff"/></svg>Location</span><span><svg viewBox="0 0 6 6"><circle cx="3" cy="3" r="3" fill="#fff"/></svg>+49 5431 987654</span><span><svg viewBox="0 0 6 6"><rect y="1" width="6" height="4" fill="#fff"/></svg>info@feldhof-agrar.de</span></div>
      <span class="logo">Feldhof</span>
      <div class="socials"><i></i><i></i><i></i><i></i></div>
    </div>
    <p class="ftr-strip">Copyright 2023 All Right Reserved</p>
  </footer>
</section>

<!-- ===== Page: Geschäftspartner ===== -->
<section class="page" style="left:702px;top:8px;height:974px">
  <header class="hdr"><span class="hdr-tab"></span><div class="hdr-bar"><span class="logo">Feldhof</span><nav class="nav"><a class="on">Landwirt</a><a>Geschäftspartner</a><a>Lieferanten</a><a>Produkte</a><a>Firmenpräsentation</a><svg viewBox="0 0 10 10"><circle cx="4" cy="4" r="3" fill="none" stroke="#fff" stroke-width="1.3"/><path d="M6.2 6.2 9 9" stroke="#fff" stroke-width="1.4"/></svg></nav></div></header>
  <div class="ph dark" role="img" aria-label="Mähdrescher im Weizenfeld, unscharf" style="left:45px;top:112px;width:473px;height:608px;border:3px solid var(--yellow);box-shadow:0 8px 30px rgba(0,0,0,.35)"></div>
  <span style="left:85px;top:145px;width:391px;height:535px;border-radius:22px;background:rgba(255,255,255,.16);border-bottom:1px solid rgba(255,255,255,.8)"></span>
  <h2 style="left:45px;width:473px;top:189px;text-align:center;color:#fff;font-size:15px;font-weight:800">Geschäftspartner</h2>
  <div style="left:45px;width:473px;top:233px;height:50px;display:flex;justify-content:center;gap:38px"><i style="position:static;width:50px;height:50px;border-radius:50%;background:var(--amber)"></i><i style="position:static;width:50px;height:50px;border-radius:50%;background:var(--amber)"></i><i style="position:static;width:50px;height:50px;border-radius:50%;background:var(--amber)"></i><i style="position:static;width:50px;height:50px;border-radius:50%;background:var(--amber)"></i></div>
  <h2 style="left:45px;width:473px;top:347px;text-align:center;color:#fff;font-size:15px;font-weight:800">Saatgutpartner</h2>
  <div style="left:45px;width:473px;top:395px;height:50px;display:flex;justify-content:center;gap:38px"><i style="position:static;width:50px;height:50px;border-radius:50%;background:var(--amber)"></i><i style="position:static;width:50px;height:50px;border-radius:50%;background:var(--amber)"></i><i style="position:static;width:50px;height:50px;border-radius:50%;background:var(--amber)"></i></div>
  <h2 style="left:45px;width:473px;top:518px;text-align:center;color:#fff;font-size:15px;font-weight:800">Equipment partners</h2>
  <div style="left:45px;width:473px;top:563px;height:50px;display:flex;justify-content:center;gap:38px"><i style="position:static;width:50px;height:50px;border-radius:50%;background:var(--amber)"></i><i style="position:static;width:50px;height:50px;border-radius:50%;background:var(--amber)"></i><i style="position:static;width:50px;height:50px;border-radius:50%;background:var(--amber)"></i><i style="position:static;width:50px;height:50px;border-radius:50%;background:var(--amber)"></i></div>

  <footer class="ftr" style="top:797px">
    <div class="ftr-body"></div>
    <div class="ftr-in">
      <span class="vline" style="left:165px"></span><span class="vline" style="left:390px"></span>
      <h3 class="ftr-title">Kontak Uns</h3>
      <span class="field" style="left:182px;top:48px;width:58px">Name</span>
      <span class="field" style="left:248px;top:48px;width:58px">Email</span>
      <span class="field" style="left:315px;top:48px;width:58px">Telefonnummer</span>
      <span class="field" style="left:182px;top:66px;width:124px;height:14px;line-height:14px">Nachricht</span>
      <span class="send">Schicken</span>
      <div class="info"><span><svg viewBox="0 0 6 6"><path d="M3 6 1 3A2 2 0 1 1 5 3Z" fill="#fff"/></svg>Location</span><span><svg viewBox="0 0 6 6"><circle cx="3" cy="3" r="3" fill="#fff"/></svg>+49 5431 987654</span><span><svg viewBox="0 0 6 6"><rect y="1" width="6" height="4" fill="#fff"/></svg>info@feldhof-agrar.de</span></div>
      <span class="logo">Feldhof</span>
      <div class="socials"><i></i><i></i><i></i><i></i></div>
    </div>
    <p class="ftr-strip">Copyright 2023 All Right Reserved</p>
  </footer>
</section>

<!-- ===== Page: Produkte ===== -->
<section class="page" style="left:1325px;top:8px;height:970px">
  <header class="hdr"><span class="hdr-tab"></span><div class="hdr-bar"><span class="logo">Feldhof</span><nav class="nav"><a class="on">Landwirt</a><a>Geschäftspartner</a><a>Lieferanten</a><a>Produkte</a><a>Firmenpräsentation</a><svg viewBox="0 0 10 10"><circle cx="4" cy="4" r="3" fill="none" stroke="#fff" stroke-width="1.3"/><path d="M6.2 6.2 9 9" stroke="#fff" stroke-width="1.4"/></svg></nav></div></header>
  <h2 style="left:0;width:556px;top:102px;text-align:center;font-size:14px;font-weight:600">Produkte</h2>
  <div class="ph seed" role="img" aria-label="Futtermittel in Säcken" style="left:106px;top:163px;width:107px;height:107px"></div>
  <div class="ph sky" role="img" aria-label="Strohballen" style="left:224px;top:163px;width:107px;height:107px"></div>
  <div class="ph hands" role="img" aria-label="Hände mit Weizen" style="left:342px;top:163px;width:107px;height:107px"></div>
  <div class="ph hands" role="img" aria-label="Hände mit Weizen" style="left:106px;top:280px;width:107px;height:107px"></div>
  <div class="ph" role="img" aria-label="Weizenähren" style="left:224px;top:280px;width:107px;height:107px"></div>
  <div class="ph green" role="img" aria-label="Getreide im Gegenlicht" style="left:342px;top:280px;width:107px;height:107px"></div>
  <div class="ph sky" role="img" aria-label="Strohballen" style="left:106px;top:396px;width:107px;height:107px"></div>
  <div class="ph green" role="img" aria-label="Getreide im Gegenlicht" style="left:224px;top:396px;width:107px;height:107px"></div>
  <div class="ph seed" role="img" aria-label="Futtermittel in Säcken" style="left:342px;top:396px;width:107px;height:107px"></div>
  <svg style="left:53px;top:325px" width="26" height="20" viewBox="0 0 26 20"><path d="M0 10 26 0V20Z" fill="var(--amber)"/></svg>
  <svg style="left:477px;top:325px" width="26" height="20" viewBox="0 0 26 20"><path d="M26 10 0 0V20Z" fill="var(--amber)"/></svg>
  <span class="btn" style="left:241px;top:527px;width:73px;height:18px;line-height:18px;font-size:8px;font-weight:600">Mehr sehen</span>
  <svg style="left:0;top:570px" width="556" height="216" viewBox="0 0 556 216"><path d="M0 0H556V216L0 141Z" fill="var(--yellow)"/></svg>
  <div style="left:85px;top:608px;width:390px;height:100px">
    <h4 style="left:0;width:110px;top:0;text-align:center;font-size:8px;font-weight:600">Lorem Ipsum</h4>
    <p style="left:0;width:118px;top:24px;text-align:center;font-size:5.6px;line-height:1.3;color:#5a4a00">Excepteur sint occaecat cupidatat non proident, sunt in Excepteur sint occaecat cupidatat non Excepteur sint occaecat cupidatat non proident, sunt in culpa , sunt in culpa</p>
    <h4 style="left:136px;width:118px;top:0;text-align:center;font-size:8px;font-weight:600">Lorem Ipsum</h4>
    <p style="left:136px;width:118px;top:24px;text-align:center;font-size:5.6px;line-height:1.3;color:#5a4a00">Excepteur sint occaecat cupidatat non proident, sunt in Excepteur sint occaecat cupidatat non Excepteur sint occaecat cupidatat non proident, sunt in culpa , sunt in culpa</p>
    <h4 style="left:272px;width:118px;top:0;text-align:center;font-size:8px;font-weight:600">Lorem Ipsum</h4>
    <p style="left:272px;width:118px;top:24px;text-align:center;font-size:5.6px;line-height:1.3;color:#5a4a00">Excepteur sint occaecat cupidatat non proident, sunt in Excepteur sint occaecat cupidatat non Excepteur sint occaecat cupidatat non proident, sunt in culpa , sunt in culpa</p>
  </div>
  <span class="btn" style="left:404px;top:725px;width:73px;height:18px;line-height:18px;background:var(--amber);font-weight:600">mehr lesen</span>

  <footer class="ftr" style="top:794px">
    <div class="ftr-body"></div>
    <div class="ftr-in">
      <span class="vline" style="left:165px"></span><span class="vline" style="left:390px"></span>
      <h3 class="ftr-title">Kontak Uns</h3>
      <span class="field" style="left:182px;top:48px;width:58px">Name</span>
      <span class="field" style="left:248px;top:48px;width:58px">Email</span>
      <span class="field" style="left:315px;top:48px;width:58px">Telefonnummer</span>
      <span class="field" style="left:182px;top:66px;width:124px;height:14px;line-height:14px">Nachricht</span>
      <span class="send">Schicken</span>
      <div class="info"><span><svg viewBox="0 0 6 6"><path d="M3 6 1 3A2 2 0 1 1 5 3Z" fill="#fff"/></svg>Location</span><span><svg viewBox="0 0 6 6"><circle cx="3" cy="3" r="3" fill="#fff"/></svg>+49 5431 987654</span><span><svg viewBox="0 0 6 6"><rect y="1" width="6" height="4" fill="#fff"/></svg>info@feldhof-agrar.de</span></div>
      <span class="logo">Feldhof</span>
      <div class="socials"><i></i><i></i><i></i><i></i></div>
    </div>
    <p class="ftr-strip">Copyright 2023 All Right Reserved</p>
  </footer>
</section>

<!-- ===== Page: Lieferanten ===== -->
<section class="page" style="left:364px;top:1000px;width:576px;height:882px">
  <header class="hdr"><span class="hdr-tab"></span><div class="hdr-bar"><span class="logo">Feldhof</span><nav class="nav"><a class="on">Landwirt</a><a>Geschäftspartner</a><a>Lieferanten</a><a>Produkte</a><a>Firmenpräsentation</a><svg viewBox="0 0 10 10"><circle cx="4" cy="4" r="3" fill="none" stroke="#fff" stroke-width="1.3"/><path d="M6.2 6.2 9 9" stroke="#fff" stroke-width="1.4"/></svg></nav></div></header>
  <div class="ph sky" role="img" aria-label="Strohballen vor hügeliger Landschaft" style="left:0;top:66px;width:576px;height:170px"></div>
  <span style="left:235px;top:127px;width:106px;height:34px;border-radius:10px;background:rgba(230,180,150,.55);font-size:16px;font-weight:500;line-height:34px;text-align:center;color:#2a1a0a">Lieferanten</span>
  <div class="ph green" role="img" aria-label="Getreide im Gegenlicht" style="left:119px;top:198px;width:108px;height:73px"></div>
  <div class="ph" role="img" aria-label="Feld mit Reihen" style="left:232px;top:198px;width:108px;height:73px"></div>
  <div class="ph dark" role="img" aria-label="Mähdrescher bei der Ernte" style="left:346px;top:198px;width:108px;height:73px"></div>
  <h3 style="left:118px;top:307px;font-family:'Archivo',sans-serif;font-size:14px;color:var(--amber)">Lorem ipsum dolor sit amet</h3>
  <p style="left:120px;top:339px;width:335px;font-size:9.5px;font-weight:500;line-height:1.22">Ut enim ad minim veniam, quis nostrud exercitation ullamco laboris nisi ut aliquip ex ea Ut enim ad minim veniam, quis nostrud exercitation ullamco laboris nisi ut aliquip ex ea commodo coUt enim ad minim veniam, quis nostrud exercitation ullamco laboris nisi ut aliquip ex ea commodo co con.</p>
  <h3 style="left:122px;top:418px;font-family:'Archivo',sans-serif;font-size:14px;color:var(--amber)">Duis aute irure dolor in reprehenderit</h3>
  <p style="left:120px;top:450px;width:335px;font-size:9.5px;font-weight:500;line-height:1.22">Ut enim ad minim veniam, quis nostrud exercitation ullamco laboris nisi ut aliquip ex ea Ut enim ad minim veniam, quis nostrud exercitation ullamco laboris nisi ut aliquip ex ea commodo coUt enim ad minim veniam, quis nostrud exercitation ullamco laboris nisi ut aliquip ex ea commodo co con.</p>
  <h3 style="left:124px;top:537px;font-family:'Archivo',sans-serif;font-size:14px;color:var(--amber)">Nemo enim ipsam voluptatem quia</h3>
  <p style="left:120px;top:569px;width:375px;font-size:9.5px;font-weight:500;line-height:1.22">Lorem ipsum dolor sit amet, consectetur adipiscing elit, sed do eiusmod tempor incididunt ut labore Lorem ipsum dolor sit amet, consectetur adipiscing elit, sed do eiusmod tempor incididunt ut labore Lorem ipsum dolor sit amet, consectetur adipiscing elit, sed do eiusmod tempor incididunt ut labore</p>

  <footer class="ftr" style="top:698px">
    <div class="ftr-body"></div>
    <div class="ftr-in">
      <span class="vline" style="left:165px"></span><span class="vline" style="left:390px"></span>
      <h3 class="ftr-title">Kontak Uns</h3>
      <span class="field" style="left:182px;top:48px;width:58px">Name</span>
      <span class="field" style="left:248px;top:48px;width:58px">Email</span>
      <span class="field" style="left:315px;top:48px;width:58px">Telefonnummer</span>
      <span class="field" style="left:182px;top:66px;width:124px;height:14px;line-height:14px">Nachricht</span>
      <span class="send">Schicken</span>
      <div class="info"><span><svg viewBox="0 0 6 6"><path d="M3 6 1 3A2 2 0 1 1 5 3Z" fill="#fff"/></svg>Location</span><span><svg viewBox="0 0 6 6"><circle cx="3" cy="3" r="3" fill="#fff"/></svg>+49 5431 987654</span><span><svg viewBox="0 0 6 6"><rect y="1" width="6" height="4" fill="#fff"/></svg>info@feldhof-agrar.de</span></div>
      <span class="logo">Feldhof</span>
      <div class="socials"><i></i><i></i><i></i><i></i></div>
    </div>
    <p class="ftr-strip">Copyright 2023 All Right Reserved</p>
  </footer>
</section>

<!-- ===== Page: Firmenpräsentation ===== -->
<section class="page" style="left:1022px;top:1028px;width:576px;height:820px">
  <header class="hdr"><span class="hdr-tab"></span><div class="hdr-bar"><span class="logo">Feldhof</span><nav class="nav"><a class="on">Landwirt</a><a>Geschäftspartner</a><a>Lieferanten</a><a>Produkte</a><a>Firmenpräsentation</a><svg viewBox="0 0 10 10"><circle cx="4" cy="4" r="3" fill="none" stroke="#fff" stroke-width="1.3"/><path d="M6.2 6.2 9 9" stroke="#fff" stroke-width="1.4"/></svg></nav></div></header>
  <div class="ph green" role="img" aria-label="Feld mit Pflanzreihen im Abendlicht" style="left:0;top:66px;width:576px;height:148px"></div>
  <p style="left:92px;top:86px;width:392px;padding:8px 6px;border-radius:10px;background:rgba(80,70,40,.45);text-align:center;font-size:9.6px;font-weight:500;line-height:1.2;color:#fff">Excepteur sint occaecat cupidatat non proident, sunt in culpa qExcepteur sint occaecat cupidatat non proident, sunt in culpa qui officia deserunt mollit anim id esExcepteur sint occaecat cupidatat non proident, sunt in culpa qui officia deserunt mollit anim id esExcepteur sint occaecat cupidatat non proident, sunt in culpa qui officia deserunt mollit anim id Excepteur sint occaecat cupidatat non proident, sunt in culpa qui officia deserunt mollit anim id es officia deserunt mollit anim id es</p>
  <svg style="left:98px;top:242px" width="378" height="116" viewBox="0 0 378 116"><path d="M0 40 Q0 34 8 33 L362 0 Q376 0 376 14 V102 Q376 116 362 116 H14 Q0 116 0 102Z" fill="var(--yellow)"/></svg>
  <svg style="left:178px;top:245px" width="22" height="22" viewBox="0 0 22 22"><path d="M11 1 20 5V11Q20 18 11 21Q2 18 2 11V5Z" fill="#111"/><path d="M7 11 10 14 15 8" stroke="#fff" stroke-width="2" fill="none"/></svg>
  <svg style="left:277px;top:243px" width="22" height="26" viewBox="0 0 22 26"><circle cx="11" cy="9" r="8" fill="#111"/><path d="M6 15 4 25 11 21 18 25 16 15Z" fill="#111"/><path d="M7 9 10 12 15 6" stroke="#fff" stroke-width="2" fill="none"/></svg>
  <svg style="left:380px;top:245px" width="22" height="22" viewBox="0 0 22 22"><circle cx="11" cy="11" r="10" fill="#111"/><path d="M6 11 10 15 16 7" stroke="var(--yellow)" stroke-width="2.4" fill="none"/></svg>
  <p style="left:150px;top:282px;width:78px;text-align:center;font-size:4.8px;line-height:1.3;color:#fff">Excepteur sint occaecat cupidatat non proident, sunt in culpa qui officia deserunt mollit anim id es Excepteur sint occaecat cupidatat non proident, sunt in culpa qui officia deserunt mollit anim id es</p>
  <p style="left:250px;top:282px;width:78px;text-align:center;font-size:4.8px;line-height:1.3;color:#fff">Excepteur sint occaecat cupidatat non proident, sunt in culpa qui officia deserunt mollit anim id es Excepteur sint occaecat cupidatat non proident, sunt in culpa qui officia deserunt mollit anim id es</p>
  <p style="left:352px;top:282px;width:78px;text-align:center;font-size:4.8px;line-height:1.3;color:#fff">Excepteur sint occaecat cupidatat non proident, sunt in culpa qui officia deserunt mollit anim id es Excepteur sint occaecat cupidatat non proident, sunt in culpa qui officia deserunt mollit anim id es</p>

  <svg style="left:0;top:388px" width="576" height="224" viewBox="0 0 576 224"><path d="M0 0H576V224L0 146Z" fill="var(--ink)"/></svg>
  <h2 style="left:140px;top:412px;font-size:14px;font-weight:500;color:#fff">Warum Uns Wählen?</h2>
  <p class="tiny" style="left:140px;top:438px;width:188px">Excepteur sint occaecat cupidatat non proident, sunt in culpa qui officia deserunt mollit anim id es</p>
  <div style="left:140px;top:462px;width:200px;height:70px">
    <i style="left:0;top:2px;width:9px;height:9px;border-radius:50%;background:var(--yellow)"></i>
    <p class="tiny" style="left:15px;top:0;width:62px"><b>Lorem Ipsum</b><br>Excepteur sint occaecat cupidatat non proident, sunt in culpa</p>
    <i style="left:90px;top:2px;width:9px;height:9px;border-radius:50%;background:var(--yellow)"></i>
    <p class="tiny" style="left:105px;top:0;width:62px"><b>Lorem Ipsum</b><br>Excepteur sint occaecat cupidatat non proident, sunt in culpa</p>
    <i style="left:0;top:38px;width:9px;height:9px;border-radius:50%;background:var(--yellow)"></i>
    <p class="tiny" style="left:15px;top:36px;width:62px"><b>Lorem Ipsum</b><br>Excepteur sint occaecat cupidatat non proident, sunt in culpa</p>
    <i style="left:90px;top:38px;width:9px;height:9px;border-radius:50%;background:var(--yellow)"></i>
    <p class="tiny" style="left:105px;top:36px;width:62px"><b>Lorem Ipsum</b><br>Excepteur sint occaecat cupidatat non proident, sunt in culpa</p>
  </div>
  <span class="btn" style="left:253px;top:542px;width:44px;height:11px"></span>
  <span style="left:355px;top:414px;width:196px;height:134px;background:var(--yellow);border-radius:4px"></span>
  <div class="ph dark" role="img" aria-label="Mähdrescher bei der Ernte" style="left:348px;top:421px;width:197px;height:133px"></div>
  <svg style="left:0;top:582px" width="576" height="58" viewBox="0 0 576 58"><path d="M0 0 576 44V58H0Z" fill="var(--yellow)"/></svg>

  <footer class="ftr" style="top:638px;height:180px">
    <div class="ftr-body"></div>
    <div class="ftr-in">
      <span class="vline" style="left:165px"></span><span class="vline" style="left:390px"></span>
      <h3 class="ftr-title">Kontak Uns</h3>
      <span class="field" style="left:182px;top:48px;width:58px">Name</span>
      <span class="field" style="left:248px;top:48px;width:58px">Email</span>
      <span class="field" style="left:315px;top:48px;width:58px">Telefonnummer</span>
      <span class="field" style="left:182px;top:66px;width:124px;height:14px;line-height:14px">Nachricht</span>
      <span class="send">Schicken</span>
      <div class="info"><span><svg viewBox="0 0 6 6"><path d="M3 6 1 3A2 2 0 1 1 5 3Z" fill="#fff"/></svg>Location</span><span><svg viewBox="0 0 6 6"><circle cx="3" cy="3" r="3" fill="#fff"/></svg>+49 5431 987654</span><span><svg viewBox="0 0 6 6"><rect y="1" width="6" height="4" fill="#fff"/></svg>info@feldhof-agrar.de</span></div>
      <span class="logo">Feldhof</span>
      <div class="socials"><i></i><i></i><i></i><i></i></div>
    </div>
    <p class="ftr-strip">Copyright 2023 All Right Reserved</p>
  </footer>
</section>

</div>
</body>
</html>
```